Modern logo for an International Trading & Consultating Company
VORKAŞ INTERNATIONAL TRADING & CONSULTING
Modern logo for an International Trading & Consultating Company - Trade
Creative Brief
Simple
KAMIR BENSOUDI
BUSINESS DEVELOPER
Telvan Koru İş Merkezi, Yeni Ilgaz Cad. No: 58 34712 Sarıyer İstanbul, Turkey
k.bensoudi@vorkas-trading.example
Company's logo

```html
<!DOCTYPE html>
<html lang="en">
<head>
<meta charset="utf-8">
<title>VORKAŞ Business Card</title>
<link href="https://fonts.googleapis.com/css2?family=Montserrat:wght@300;400;500&display=swap" rel="stylesheet">
<style>
  :root {
    --page-bg: #ffffff;
    --card-light: #f1f1f0;
    --card-dark: #35302d;
    --gold: #c9a25a;
    --ink: #5a5552;
    --ink-soft: #7d7874;
    --white: #f4f2ef;
    --divider: #b9b4ae;
  }
  * { margin: 0; padding: 0; box-sizing: border-box; }
  html, body { width: 1200px; height: 763px; overflow: hidden; background: var(--page-bg); }
  body { position: relative; font-family: "Montserrat", sans-serif; }

  .card { position: absolute; box-shadow: 0 4px 14px rgba(0,0,0,0.18); }
  .card-front { left: 355px; top: 43px; width: 490px; height: 293px; background: var(--card-light); }
  .card-back { left: 355px; top: 420px; width: 495px; height: 295px; background: var(--card-dark); }

  .brand { position: absolute; text-align: center; font-family: "Montserrat", sans-serif; font-weight: 300; }
  .brand-name { display: block; letter-spacing: 0.06em; line-height: 1; }
  .brand-tagline { display: block; letter-spacing: 0.18em; line-height: 1; }

  .card-front .brand { left: 30px; top: 150px; width: 176px; color: var(--ink); }
  .card-front .brand-name { font-size: 34px; }
  .card-front .brand-tagline { font-size: 5px; margin-top: 7px; }

  .divider { position: absolute; left: 214px; top: 82px; width: 1px; height: 147px; background: var(--divider); }

  .contact { position: absolute; left: 231px; top: 87px; color: var(--ink-soft); font-size: 7.5px; line-height: 1.55; }
  .contact-name { color: var(--gold); font-size: 10px; font-weight: 500; letter-spacing: 0.08em; }
  .contact-role { font-size: 7px; letter-spacing: 0.06em; margin-bottom: 16px; }
  .contact-address { margin-bottom: 8px; max-width: 230px; }
  .contact-line { display: flex; align-items: center; gap: 5px; }
  .contact-line svg { width: 8px; height: 8px; flex: none; }

  .card-back .brand { left: 0; top: 135px; width: 100%; color: var(--white); }
  .card-back .brand-name { font-size: 50px; }
  .card-back .brand-tagline { font-size: 7.5px; margin-top: 12px; letter-spacing: 0.3em; }
</style>
</head>
<body>
  <section class="card card-front">
    <div class="brand">
      <span class="brand-name">VORKAŞ</span>
      <span class="brand-tagline">INTERNATIONAL TRADING &amp; CONSULTING</span>
    </div>
    <div class="divider"></div>
    <div class="contact">
      <p class="contact-name">KAMIR BENSOUDI</p>
      <p class="contact-role">BUSINESS DEVELOPER</p>
      <p class="contact-address">Telvan Koru İş Merkezi, Yeni Ilgaz Cad. No: 58<br>34712 Sarıyer<br>İstanbul, Turkey</p>
      <p class="contact-line">
        <svg viewBox="0 0 10 10" aria-hidden="true"><path d="M2 1l2 2-1 1.2a6 6 0 0 0 2.8 2.8L7 6l2 2-1.3 1.3C4.5 9 1 5.5.7 2.3z" fill="var(--gold)"/></svg>
        +905320004718
      </p>
      <p class="contact-line">
        <svg viewBox="0 0 10 10" aria-hidden="true"><rect x="0.5" y="2" width="9" height="6" fill="none" stroke="var(--gold)"/><path d="M.5 2l4.5 3.5L9.5 2" fill="none" stroke="var(--gold)"/></svg>
        k.bensoudi@vorkas-trading.example
      </p>
    </div>
  </section>

  <section class="card card-back">
    <div class="brand">
      <span class="brand-name">VORKAŞ</span>
      <span class="brand-tagline">INTERNATIONAL TRADING &amp; CONSULTING</span>
    </div>
  </section>
</body>
</html>
```